Irrigation Business needs their business cards modernised and revamped

I would like to keep my current logo, colours and revamp the format of the card.

I would like the card to be clean yet important.

Im not sure if you include texture but i would like the named logo to be indented into the card etc.

show me something alive and free something thats clinical to the point yet has a feel of achievement. i would like people to go nice card.

Target Market(s)

high end clients, corporate, sports field manger, the guys that make the decisions

Industry/Entity Type

Business

Contact Information for Business Card

nformation to be included

Dean Harlow (Director)
0487305526
dean@kolvat.biz
www.kestonfieldworks.com

instagram logo
google logo
facebook logo

Colors

Designer to choose colors to be used in the design.

Requirements
Nice to have
• indentations a really nice feel to the card good texture

```html
<!DOCTYPE html>
<html lang="en">
<head>
<meta charset="utf-8">
<title>Keston Fieldworks – Business Card</title>
<link rel="stylesheet" href="https://fonts.googleapis.com/css2?family=Heebo:wght@400;500&display=swap">
<style>
  :root {
    --page: #e9e5df;
    --card-blue-deep: #1f4f82;
    --card-blue: #2f6ea3;
    --card-frost: #d9d6d0;
    --silver: #e6ded2;
    --silver-soft: #d3cbbd;
    --mark-ring: #2a5b95;
    --mark-fill: #2596a6;
  }
  * { box-sizing: border-box; margin: 0; padding: 0; }
  html, body {
    width: 1200px;
    height: 1047px;
    overflow: hidden;
    background: var(--page);
    font-family: "Heebo", Arial, sans-serif;
  }
  .business-card {
    position: absolute;
    left: 100px;
    top: 243px;
    width: 1000px;
    height: 560px;
    border-radius: 26px;
    overflow: hidden;
    background: linear-gradient(90deg,
      var(--card-blue-deep) 0%,
      var(--card-blue) 45%,
      #4f83b3 62%,
      var(--card-frost) 80%);
    box-shadow: 0 18px 40px rgba(40, 40, 40, 0.18);
  }
  .brand-name {
    position: absolute;
    left: 64px;
    top: 44px;
    color: var(--silver);
    font-weight: 500;
    text-transform: uppercase;
    line-height: 1;
  }
  .brand-name .primary { display: block; font-size: 33px; letter-spacing: 0.5px; }
  .brand-name .secondary { display: block; font-size: 21px; letter-spacing: 6px; margin-top: 6px; padding-left: 68px; }
  .person {
    position: absolute;
    left: 64px;
    top: 222px;
    color: var(--silver);
  }
  .person-name { font-size: 30px; font-weight: 500; text-transform: uppercase; letter-spacing: 0.5px; }
  .person-role { font-size: 22px; font-weight: 400; color: var(--silver-soft); margin-top: 4px; }
  .person-rule { width: 28px; height: 2px; background: var(--silver); margin-top: 18px; }
  .contact-list {
    position: absolute;
    left: 64px;
    top: 345px;
    list-style: none;
    color: var(--silver-soft);
    font-size: 21px;
  }
  .contact-list li { display: flex; align-items: center; height: 31px; }
  .contact-list svg { width: 20px; height: 20px; margin-right: 26px; }
  .social-row {
    position: absolute;
    left: 62px;
    top: 482px;
    display: flex;
    gap: 10px;
  }
  .social-dot { width: 26px; height: 26px; border-radius: 50%; background: var(--silver-soft); }
  .brand-mark {
    position: absolute;
    left: 449px;
    top: 10px;
    width: 540px;
    height: 540px;
  }
  .brand-mark-text {
    position: absolute;
    left: 449px;
    top: 10px;
    width: 540px;
    height: 540px;
    display: flex;
    flex-direction: column;
    align-items: center;
    justify-content: center;
    color: var(--silver);
    font-weight: 500;
    text-transform: uppercase;
  }
  .brand-mark-text .primary { font-size: 62px; letter-spacing: 2px; line-height: 1; }
  .brand-mark-text .secondary { font-size: 30px; letter-spacing: 9px; margin-top: 12px; }
</style>
</head>
<body>
  <section class="business-card">
    <div class="brand-name">
      <span class="primary">Keston Fieldworks</span>
    </div>

    <div class="person">
      <p class="person-name">Dean Harlow</p>
      <p class="person-role">Director</p>
      <div class="person-rule"></div>
    </div>

    <ul class="contact-list">
      <li>
        <svg viewBox="0 0 20 20" aria-hidden="true"><path d="M5 3l3 3-2 2c1 2 3 4 5 5l2-2 3 3-2 3C8 17 3 12 2 5z" fill="var(--silver-soft)"/></svg>
        0487305526
      </li>
      <li>
        <svg viewBox="0 0 20 20" aria-hidden="true"><rect x="2" y="4" width="16" height="12" fill="var(--silver-soft)"/><path d="M2 4l8 7 8-7" fill="none" stroke="var(--card-blue)" stroke-width="1.5"/></svg>
        dean@kolvat.biz
      </li>
      <li>
        <svg viewBox="0 0 20 20" aria-hidden="true" fill="none" stroke="var(--silver-soft)" stroke-width="1.5"><circle cx="10" cy="10" r="8"/><ellipse cx="10" cy="10" rx="3.5" ry="8"/><path d="M2 10h16M3.5 6h13M3.5 14h13"/></svg>
        www.kestonfieldworks.com
      </li>
    </ul>

    <div class="social-row" role="img" aria-label="Social media profiles">
      <span class="social-dot"></span>
      <span class="social-dot"></span>
      <span class="social-dot"></span>
    </div>

    <svg class="brand-mark" viewBox="0 0 540 540" aria-hidden="true">
      <circle cx="270" cy="270" r="262" fill="var(--mark-ring)"/>
      <circle cx="270" cy="270" r="238" fill="var(--mark-fill)"/>
    </svg>
    <div class="brand-mark-text">
      <span class="primary">Keston</span>
      <span class="secondary">Fieldworks</span>
    </div>
  </section>
</body>
</html>
```